Awesome photographers card for an awesome new business

Double sided business card Black background and silver logo in middle on one side. Details on otherside. please keep it simple

Industry/Entity Type

Photographer

Contact Information for Business Card

Gerald Fenwick
0452817360
GeraldFenwickPhotography47@mailbox.test
www.GeraldFenwickPhotography.test.au
Instagram _Gerald_fenwick

Requirements
Must have
• My logo in Silver
• please use instagram logo instead of "Instagram"

```html
<!DOCTYPE html>
<html lang="en">
<head>
<meta charset="utf-8">
<title>Gerald Fenwick Photography – Business Card</title>
<link rel="stylesheet" href="https://fonts.googleapis.com/css2?family=Roboto:wght@400;500&family=Roboto+Condensed:wght@500&display=swap">
<style>
  :root {
    --backdrop: #2b2b2b;
    --card-black: #151516;
    --silver-light: #d2d2d2;
    --silver-mid: #a9a9a9;
    --silver-dark: #7e7e7e;
    --text-light: #ffffff;
    --logo-silver: #cfcfcf;
    --logo-dark: #3a3a3a;
  }
  * { margin: 0; padding: 0; box-sizing: border-box; }
  html, body { width: 1200px; height: 960px; overflow: hidden; }
  body { background: var(--backdrop); position: relative; font-family: "Roboto", sans-serif; }

  .card {
    position: absolute;
    width: 598px;
    height: 342px;
    overflow: hidden;
    box-shadow: 0 6px 14px rgba(0,0,0,.45);
  }
  .card--front { left: 315px; top: 113px; }
  .card--back {
    left: 311px; top: 472px;
    background: radial-gradient(ellipse at 50% 20%, var(--silver-light) 0%, var(--silver-mid) 55%, var(--silver-dark) 100%);
  }
  .card__shape { position: absolute; inset: 0; }

  .logo-mark {
    position: absolute;
    display: flex;
    align-items: center;
    justify-content: center;
    border-radius: 50%;
    font-family: "Roboto", sans-serif;
    font-weight: 500;
    text-align: center;
    letter-spacing: 2px;
    text-transform: uppercase;
  }
  .card--front .logo-mark {
    left: 62px; top: 40px; width: 164px; height: 164px;
    border: 3px solid var(--logo-silver);
    color: var(--logo-silver);
    font-size: 17px;
    line-height: 1.3;
  }
  .card--back .logo-mark {
    left: 212px; top: 96px; width: 172px; height: 172px;
    border: 3px solid var(--logo-dark);
    color: var(--logo-dark);
    font-size: 18px;
    line-height: 1.3;
  }

  .holder-name {
    position: absolute;
    right: 30px; top: 45px;
    font-family: "Roboto Condensed", sans-serif;
    font-weight: 500;
    font-size: 21px;
    color: var(--text-light);
    text-transform: uppercase;
  }
  .contact-list {
    position: absolute;
    right: 32px; top: 236px;
    list-style: none;
    color: var(--text-light);
    font-size: 14px;
    line-height: 19px;
    text-align: right;
  }
  .contact-list li { display: flex; justify-content: flex-end; align-items: center; gap: 7px; }
  .contact-icon { width: 13px; height: 13px; flex: none; }

  .back-website {
    position: absolute;
    left: 0; right: 0; top: 291px;
    text-align: center;
    color: var(--text-light);
    font-size: 15px;
    letter-spacing: 2.4px;
  }
</style>
</head>
<body>

  <section class="card card--front" aria-label="Business card front">
    <svg class="card__shape" viewBox="0 0 598 342" width="598" height="342" aria-hidden="true">
      <defs>
        <linearGradient id="silverPanel" x1="0" y1="0" x2="1" y2="1">
          <stop offset="0" stop-color="#9a9a9a"/>
          <stop offset=".45" stop-color="#b9b9b9"/>
          <stop offset="1" stop-color="#8a8a8a"/>
        </linearGradient>
        <linearGradient id="edgeLine" x1="0" y1="0" x2="0" y2="1">
          <stop offset="0" stop-color="#6d6d6d"/>
          <stop offset=".5" stop-color="#f2f2f2"/>
          <stop offset="1" stop-color="#7a7a7a"/>
        </linearGradient>
      </defs>
      <rect width="598" height="342" fill="url(#silverPanel)"/>
      <path d="M0 0 H386 C350 4 330 30 312 105 L246 342 H0 Z" fill="#5b5b5b"/>
      <path d="M0 0 H376 C342 4 322 30 304 105 L238 342 H0 Z" fill="var(--card-black)"/>
      <path d="M382 0 C348 4 328 30 309 105 L243 342" fill="none" stroke="url(#edgeLine)" stroke-width="2.5"/>
    </svg>

    <div class="logo-mark">Gerald<br>Fenwick</div>

    <h1 class="holder-name">Gerald Fenwick</h1>

    <ul class="contact-list">
      <li>0452817360
        <svg class="contact-icon" viewBox="0 0 16 16" aria-label="Phone"><path fill="#fff" d="M3.6 1.2l2.3 2.6-1.3 2c.8 1.9 2.5 3.6 4.4 4.4l2-1.3 2.6 2.3-1.3 2.3C7 13.2 2.8 9 2 3.2z"/></svg>
      </li>
      <li>GeraldFenwickPhotography47@mailbox.test
        <svg class="contact-icon" viewBox="0 0 16 16" aria-label="Email"><rect x="1" y="3" width="14" height="10" fill="#fff"/><path d="M1.5 3.5L8 9l6.5-5.5" fill="none" stroke="#9a9a9a" stroke-width="1.3"/></svg>
      </li>
      <li>www.GeraldFenwickPhotography.test.au
        <svg class="contact-icon" viewBox="0 0 16 16" aria-label="Website"><circle cx="8" cy="8" r="6.5" fill="#fff"/><path d="M1.5 8h13M8 1.5c-3 3.5-3 9.5 0 13M8 1.5c3 3.5 3 9.5 0 13" fill="none" stroke="#9a9a9a" stroke-width="1"/></svg>
      </li>
      <li>Gerald_fenwick
        <svg class="contact-icon" viewBox="0 0 16 16" aria-label="Instagram"><rect x="1" y="1" width="14" height="14" rx="2" fill="#fff"/></svg>
      </li>
    </ul>
  </section>

  <section class="card card--back" aria-label="Business card back">
    <div class="logo-mark">Gerald<br>Fenwick</div>
    <p class="back-website">www.GeraldFenwickPhotography.test.au</p>
  </section>

</body>
</html>
```